Business Card - high end, modern health care

Hey designers!

We need a double sided business card for the boutique, cutting edge physical therapy rehabilitation centre in Sydney's Northern Beaches.

With the most qualified physios in the area The Harbourview Motion Clinic does what other physiotherapy practices do not, we take our time with our patients giving them longer appointments, better physios and therefor faster results!

We guarantee that the service people receive at THMC will be unparalleled.

Hence we need a business card to reflect our modern, boutique, high end service. The final design needs to reflect that we are in a class of our own yet with the feel of beachside retreat.

Below I have attached our logo in both blue on white and white on blue. The exact colour is;
and the font that we have used in our logo is Tex Gyre Aventador.

I like the idea of the blue as the main colour as it is more eye catching and our signage onto the main road will be in this blue and in the interest of consistency across marketing the blue needs to be a part of the design. However I would appreciate a few designs onto a wooden background as this is a visual theme within the fitout of the practice.

The design needs to be of standard size (91x55mm).

Target Market(s)

We target people who have an end outcome in mind and those who have had poor experiences with other providers and ensure that everyone gets the care that they deserve with a premium service that is tailored to the individuals circumstances. As a premium service, the target market is highly educated, business and tech savvy with the additional target market of elderly people who have self funded their retirement and see value in paying for the best ongoing rehabilitation to maintain independence.

Industry/Entity Type

Physical Therapy

Contact Information for Business Card

Name, designation( Titled Musculoskeletal Physiotherapist... there will also be those in the company that have multiple designations ie 5 or 6 words long), phone number, email, facebook, instagram, address

Font styles to use
Sans Serif

Colors

Designer to choose colors to be used in the design.

Requirements
Must have
• Front - The logo as large as possible, blue or wooden theme, and all of the important details.
• Back - A blank space/lines on which to write appointment times (no "Appointment, date, time" etc.)
Nice to have
• facebook url
• logos for facebook and instagram
• Mini logos for the phone and email?

```html
<!DOCTYPE html>
<html lang="en">
<head>
<meta charset="utf-8">
<title>The Harbourview Motion Clinic – Business Card</title>
<link rel="stylesheet" href="https://fonts.googleapis.com/css2?family=Montserrat:wght@400;500;700&display=swap">
<style>
  :root {
    --brand-blue: #1158a7;
    --paper-white: #ffffff;
    --back-paper: #eceef1;
    --back-art: #e2e6ec;
    --rule-grey: #6b6f75;
    --stage: #262626;
  }
  html, body {
    margin: 0;
    padding: 0;
    width: 1200px;
    height: 960px;
    overflow: hidden;
    background: var(--stage);
    font-family: "Montserrat", sans-serif;
  }
  .canvas {
    position: relative;
    width: 1200px;
    height: 960px;
  }
  .card {
    position: absolute;
    width: 598px;
    height: 342px;
    border-radius: 16px;
    overflow: hidden;
  }
  .card--front {
    left: 322px;
    top: 108px;
    background: var(--brand-blue);
    color: var(--paper-white);
  }
  .card--back {
    left: 320px;
    top: 493px;
    background: var(--back-paper);
  }

  /* Front */
  .brand-artwork {
    position: absolute;
    left: 292px;
    top: 14px;
    width: 294px;
    height: 314px;
    border-radius: 0 14px 0 0;
    background: linear-gradient(135deg, #ffffff 0%, #d7e4f3 55%, #2c6cb5 100%);
  }
  .wordmark-front {
    position: absolute;
    left: 30px;
    top: 41px;
  }
  .wordmark-main {
    display: block;
    font-weight: 700;
    font-size: 23px;
    line-height: 1;
    letter-spacing: -0.2px;
  }
  .wordmark-sub {
    display: block;
    font-weight: 500;
    font-size: 15px;
    letter-spacing: 5.4px;
    margin-top: 3px;
  }
  .person {
    position: absolute;
    left: 30px;
    top: 104px;
  }
  .person-name {
    margin: 0;
    font-weight: 700;
    font-size: 22px;
    line-height: 1;
  }
  .person-title {
    margin: 5px 0 0;
    font-size: 14px;
    letter-spacing: 0.3px;
  }
  .address {
    position: absolute;
    left: 30px;
    top: 161px;
    margin: 0;
    font-style: normal;
    font-size: 14px;
    line-height: 19px;
  }
  .contact-list {
    position: absolute;
    left: 30px;
    top: 210px;
    margin: 0;
    padding: 0;
    list-style: none;
    font-size: 14px;
    line-height: 19px;
  }
  .contact-list li {
    display: flex;
    align-items: center;
  }
  .contact-icon {
    width: 13px;
    height: 13px;
    margin-right: 11px;
    flex: none;
  }
  .contact-icon--square,
  .contact-icon--circle {
    width: 11px;
    height: 11px;
    margin: 0 12px 0 1px;
    background: var(--paper-white);
    flex: none;
  }
  .contact-icon--square { border-radius: 1px; }
  .contact-icon--circle { border-radius: 50%; }

  /* Back */
  .back-artwork {
    position: absolute;
    left: 255px;
    top: 14px;
    width: 330px;
    height: 314px;
    border-radius: 0 14px 0 0;
    background: linear-gradient(135deg, var(--back-paper) 0%, var(--back-art) 100%);
  }
  .wordmark-back {
    position: absolute;
    left: 0;
    right: 0;
    top: 46px;
    display: flex;
    justify-content: center;
    align-items: center;
    color: var(--brand-blue);
  }
  .wordmark-dot {
    width: 40px;
    height: 40px;
    border-radius: 50%;
    background: var(--brand-blue);
    margin-right: 12px;
    flex: none;
  }
  .appointment-lines {
    position: absolute;
    left: 38px;
    top: 142px;
    width: 520px;
  }
  .appointment-line {
    height: 40px;
    border-bottom: 1px solid var(--rule-grey);
    box-sizing: border-box;
  }
  .appointment-line:first-child {
    height: 1px;
  }
</style>
</head>
<body>
<main class="canvas">

  <section class="card card--front" aria-label="Business card front">
    <div class="brand-artwork" role="img" aria-label="Large brand artwork area"></div>

    <div class="wordmark-front">
      <span class="wordmark-main">THE HARBOURVIEW</span>
      <span class="wordmark-sub">MOTION CLINIC</span>
    </div>

    <div class="person">
      <h1 class="person-name">DANIEL REYES</h1>
      <p class="person-title">CEO/FOUNDER</p>
    </div>

    <address class="address">14 Seacliff Parade<br>Dee Why NSW 2099</address>

    <ul class="contact-list">
      <li>
        <svg class="contact-icon" viewBox="0 0 16 16" aria-hidden="true">
          <path fill="#fff" d="M3.6 1.2 5.8 3.4c.4.4.4 1 0 1.4L4.7 5.9c.8 1.9 2.4 3.5 4.3 4.3l1.1-1.1c.4-.4 1-.4 1.4 0l2.2 2.2c.4.4.4 1 0 1.4l-1.3 1.3c-.6.6-1.6.8-2.4.4C6.6 13 3 9.4 1.6 6 1.2 5.2 1.4 4.2 2 3.6L3.3 2.3c.1-.4-.1-.8.3-1.1Z"/>
        </svg>
        02 9981 4470
      </li>
      <li>
        <svg class="contact-icon" viewBox="0 0 16 16" aria-hidden="true">
          <rect x="1" y="3" width="14" height="10" rx="1" fill="#fff"/>
          <path d="M1.5 3.8 8 9l6.5-5.2" fill="none" stroke="#1158a7" stroke-width="1.3"/>
        </svg>
        daniel@hvmotion.com
      </li>
      <li>
        <svg class="contact-icon" viewBox="0 0 16 16" aria-hidden="true">
          <circle cx="8" cy="8" r="6.5" fill="none" stroke="#fff" stroke-width="1.5"/>
          <ellipse cx="8" cy="8" rx="2.8" ry="6.5" fill="none" stroke="#fff" stroke-width="1.2"/>
          <path d="M1.5 8h13" stroke="#fff" stroke-width="1.2"/>
        </svg>
        www.hvmotion.com
      </li>
      <li><span class="contact-icon--square" aria-hidden="true"></span>/hvmotionclinic</li>
      <li><span class="contact-icon--circle" aria-hidden="true"></span>@hvmotionclinic</li>
    </ul>
  </section>

  <section class="card card--back" aria-label="Business card back">
    <div class="back-artwork" role="img" aria-label="Faint brand artwork area"></div>

    <div class="wordmark-back">
      <span class="wordmark-dot" aria-hidden="true"></span>
      <div>
        <span class="wordmark-main">THE HARBOURVIEW</span>
        <span class="wordmark-sub">MOTION CLINIC</span>
      </div>
    </div>

    <div class="appointment-lines" aria-label="Lines for appointment notes">
      <div class="appointment-line"></div>
      <div class="appointment-line"></div>
      <div class="appointment-line"></div>
      <div class="appointment-line"></div>
      <div class="appointment-line"></div>
    </div>
  </section>

</main>
</body>
</html>
```